Business Card Design for Software Development Company

I am looking for a business card design the incorporates my new logo (attached below).

Key information to include:
Name: Martin Quelbrook
Title: CEO
Email: martin@brightwellcivic.example
Phone: 555-218-9403
Website: www.brightwellcivic.example

NOTE: This design should be easy to edit so that we can order cards for different members of our team.

```html
<!DOCTYPE html>
<html lang="en">
<head>
<meta charset="utf-8">
<title>Brightwell Labs – Business Card</title>
<link href="https://fonts.googleapis.com/css2?family=Montserrat:wght@400;600;700&display=swap" rel="stylesheet">
<style>
  :root {
    --backdrop: #959595;
    --navy: #373f56;
    --white: #ffffff;
    --accent: #e8792a;
    --ink: #1f2433;
  }
  * { box-sizing: border-box; margin: 0; padding: 0; }
  html, body {
    width: 1200px; height: 1108px; overflow: hidden;
    background: var(--backdrop);
    font-family: "Montserrat", sans-serif;
  }
  .canvas { position: relative; width: 1200px; height: 1108px; }
  .card {
    position: absolute; left: 241px; width: 740px; height: 423px;
    border-radius: 36px; overflow: hidden;
  }
  .card--front { top: 117px; background: var(--navy); }
  .card--back { top: 578px; background: var(--white); }

  .brand {
    position: absolute; left: 72px; top: 168px;
    display: flex; align-items: center; gap: 14px;
  }
  .card--back .brand { top: 110px; }
  .brand__mark { width: 40px; height: 40px; background: var(--accent); flex: none; }
  .brand__lockup { display: flex; flex-direction: column; align-items: flex-end; }
  .brand__name {
    font-weight: 600; font-size: 62px; line-height: 1; letter-spacing: -1px;
    color: var(--white);
  }
  .brand__tagline {
    margin-top: 6px; font-weight: 600; font-size: 9.5px; letter-spacing: 0.4px;
    color: var(--white);
  }
  .card--back .brand__name,
  .card--back .brand__tagline { color: var(--navy); }

  .person {
    position: absolute; right: 428px; top: 250px; text-align: right;
  }
  .person__name { font-weight: 700; font-size: 29px; color: var(--navy); line-height: 1.15; }
  .person__title { font-weight: 400; font-size: 20px; color: var(--ink); }

  .divider {
    position: absolute; left: 340px; top: 243px; width: 1.5px; height: 98px;
    background: var(--navy);
  }

  .contact { position: absolute; left: 364px; top: 246px; list-style: none; }
  .contact__item {
    display: flex; align-items: center; gap: 12px; height: 29.5px;
    font-size: 19.5px; color: var(--ink);
  }
  .contact__icon { width: 21px; height: 21px; flex: none; fill: var(--navy); }
</style>
</head>
<body>
<main class="canvas">
  <section class="card card--front" aria-label="Card front">
    <div class="brand">
      <span class="brand__mark"></span>
      <div class="brand__lockup">
        <span class="brand__name">Brightwell Labs</span>
        <span class="brand__tagline">A DIVISION OF BRIGHTWELL CIVIC</span>
      </div>
    </div>
  </section>

  <section class="card card--back" aria-label="Card back">
    <div class="brand">
      <span class="brand__mark"></span>
      <div class="brand__lockup">
        <span class="brand__name">Brightwell Labs</span>
        <span class="brand__tagline">A DIVISION OF BRIGHTWELL CIVIC</span>
      </div>
    </div>

    <div class="person">
      <p class="person__name">Martin Quelbrook</p>
      <p class="person__title">CEO</p>
    </div>

    <span class="divider"></span>

    <ul class="contact">
      <li class="contact__item">
        <svg class="contact__icon" viewBox="0 0 24 24" aria-hidden="true"><path d="M6.6 10.8c1.4 2.8 3.8 5.1 6.6 6.6l2.2-2.2c.3-.3.7-.4 1-.2 1.1.4 2.3.6 3.6.6.6 0 1 .4 1 1V20c0 .6-.4 1-1 1C10.6 21 3 13.4 3 4c0-.6.4-1 1-1h3.5c.6 0 1 .4 1 1 0 1.3.2 2.5.6 3.6.1.3 0 .7-.2 1z"/></svg>
        <span>555-218-9403</span>
      </li>
      <li class="contact__item">
        <svg class="contact__icon" viewBox="0 0 24 24" aria-hidden="true"><path d="M2 5h20v14H2z M3.5 6.5 12 12.5l8.5-6v-.2h-17z" fill-rule="evenodd"/><path d="M2 5l10 7 10-7v2l-10 7L2 7z" fill="#fff"/></svg>
        <span>martin@brightwellcivic.example</span>
      </li>
      <li class="contact__item">
        <svg class="contact__icon" viewBox="0 0 24 24" aria-hidden="true"><path d="M12 2a10 10 0 1 0 0 20 10 10 0 0 0 0-20zm0 2c1 0 2 .2 2.9.5L13 6l-2 1 1 2-3 1-1-2-2.6-.4A8 8 0 0 1 12 4zm-7.6 6.5L7 12l1 3-1 2a8 8 0 0 1-2.6-6.5zM14 19.8l1-3.8 3-1 1.3 1.6A8 8 0 0 1 14 19.8z"/></svg>
        <span>www.brightwellcivic.example</span>
      </li>
    </ul>
  </section>
</main>
</body>
</html>
```